Prepared Meal Company Needs Menu Design

We are a pre-prepared meal delivery company called Grubb Larder.

We have a menu in excel but needs to be designed to look good and appealing to customers. The menu should be clean, easy to ready, and show:Title (Pupusa)Tags (V, V+, GF - Use a cool vegan logo for the V+ and logo for vegetarian V symbol)Price (12.99)DescriptionBrand colors are orange white and green. Design is clean, crisp and can incorporate natural elements like leaf shaped symbols, etc. Screenshots from our website attached for inspiration.

Target Market(s)

Broad demographics

Industry/Entity Type

Restaurant

Font styles to use
Sans Serif

Requirements
Must have
• The menu design should be commensurate with the website under development
• https://grubblarder.dishboard.example
Nice to have
• Should have appropriate graphics
Should not have
• Modifiers do not need to be shown (these are shown in the excel only).

```html
<!DOCTYPE html>
<html lang="en">
<head>
<meta charset="utf-8">
<title>Grubb Larder Menu</title>
<link href="https://fonts.googleapis.com/css2?family=Archivo:ital,wght@0,400;0,600;0,700;0,800;1,400&display=swap" rel="stylesheet">
<style>
:root{
  --orange:#fc6a0c;
  --green:#0e8a3c;
  --ink:#3a3a3a;
  --paper:#ffffff;
  --bg:#ffffff;
  --rule:#8a8a8a;
}
*{box-sizing:border-box;margin:0;padding:0}
html,body{width:1200px;height:2604px;overflow:hidden;background:var(--bg);font-family:"Archivo",Arial,sans-serif;color:var(--ink)}
.page{position:absolute;left:92px;width:1015px;height:1228px;background:var(--paper);box-shadow:0 6px 16px rgba(0,0,0,.28);overflow:hidden}
.page-one{top:70px}
.page-two{top:1344px}
.page-foot{position:absolute;left:0;right:0;bottom:0;height:24px;background:var(--green)}
.brand{position:absolute;left:862px;top:20px;width:132px;height:132px;border:4px solid var(--orange);border-radius:50%;display:flex;align-items:center;justify-content:center;text-align:center;color:var(--orange);font-weight:700;font-size:19px;line-height:1.1}
.section-bar{position:absolute;left:0;height:34px;padding-left:40px;background:var(--orange);color:#fff;font-weight:800;font-size:22px;line-height:34px;clip-path:polygon(0 0,calc(100% - 22px) 0,100% 50%,calc(100% - 22px) 100%,0 100%)}
.menu-list{position:absolute;left:0;right:0}
.item{position:relative;padding-bottom:22px}
.item::after{content:"";position:absolute;left:129px;width:762px;bottom:9px;border-top:2px dashed var(--rule)}
.item.last::after{display:none}
.item-name{margin-left:98px;color:var(--green);font-weight:700;font-size:19px;line-height:23px}
.item-desc{margin-left:98px;margin-top:3px;width:360px;font-style:italic;font-size:12px;line-height:15px;color:#333}
.tag-icon{position:absolute;left:617px;top:-6px;width:42px;height:42px}
.tag-icon.lower{top:46px}
.tag-text{position:absolute;left:664px;top:4px;font-weight:700;font-size:15.5px;line-height:22px;color:var(--ink);white-space:nowrap}
.tag-text.lower{top:56px}
.tag-text.wide{left:712px}
.price{position:absolute;right:112px;top:2px;font-weight:700;font-size:19px;line-height:23px;color:var(--ink)}
</style>
</head>
<body>
<svg width="0" height="0" style="position:absolute">
  <defs>
    <symbol id="badge-veg" viewBox="0 0 42 42">
      <circle cx="21" cy="21" r="17" fill="none" stroke="#0e8a3c" stroke-width="6" stroke-dasharray="3.4 2"/>
      <circle cx="21" cy="21" r="14" fill="#fff" stroke="#0e8a3c" stroke-width="2"/>
      <text x="21" y="28" text-anchor="middle" font-family="Archivo,Arial,sans-serif" font-weight="800" font-style="italic" font-size="19" fill="#0e8a3c">V</text>
    </symbol>
    <symbol id="badge-vegan" viewBox="0 0 42 42">
      <circle cx="21" cy="21" r="17" fill="none" stroke="#0e8a3c" stroke-width="6" stroke-dasharray="3.4 2"/>
      <circle cx="21" cy="21" r="15" fill="#0e8a3c"/>
      <circle cx="21" cy="21" r="12" fill="none" stroke="#fff" stroke-width="1"/>
      <text x="21" y="24.5" text-anchor="middle" font-family="Archivo,Arial,sans-serif" font-weight="800" font-size="7.5" fill="#fff">VEGAN</text>
    </symbol>
  </defs>
</svg>

<section class="page page-one">
  <div class="brand">Grubb<br>Larder</div>
  <div class="section-bar" style="top:105px;width:498px">BREAKFAST &nbsp;- All Menu Items Soy Free</div>

  <div class="menu-list" style="top:168px">
    <div class="item" style="min-height:96px">
      <h3 class="item-name">Cinnamon-Apple Sunrise Oats</h3>
      <p class="item-desc">Almond Milk &amp; Ceylon Cinnamon, Marinated Golden Raisins, Macca Powder, Apple-Pecan Crumble</p>
      <svg class="tag-icon"><use href="#badge-vegan"/></svg><span class="tag-text">GF</span>
      <span class="price">6.99</span>
    </div>
    <div class="item" style="min-height:98px">
      <h3 class="item-name">Acai Yogurt</h3>
      <p class="item-desc">Coconut, Goji, Seasonal Fruit, Crunchy Chia Seeds, Ceylon Cinnamon</p>
      <svg class="tag-icon"><use href="#badge-veg"/></svg><span class="tag-text">GF</span>
      <span class="price">7.99</span>
    </div>
    <div class="item" style="min-height:94px">
      <h3 class="item-name">Sprouted 7-Grain Cereal &amp; Yogurt</h3>
      <p class="item-desc">Apricot-Pear Compote, Almond &amp; Saba Drizzle</p>
      <svg class="tag-icon"><use href="#badge-veg"/></svg>
      <span class="price">7.49</span>
    </div>
    <div class="item" style="min-height:76px">
      <h3 class="item-name">St. Benedict's Eggs</h3>
      <p class="item-desc">2 Soft Yolk Eggs over Rosemary Polenta, Caramelized Onion, Mushrooms &amp; Asparagus, Lemon</p>
      <svg class="tag-icon"><use href="#badge-veg"/></svg><span class="tag-text wide">Dairy Free</span>
      <span class="price">9.49</span>
    </div>
    <div class="item" style="min-height:108px">
      <h3 class="item-name">Pomegranate &amp; Saffron Shakshuka</h3>
      <p class="item-desc">2 Soft Yolk Eggs over Roasted Tomatoes, Onions &amp; Peppers, Garden Herb Oil, Rosemary, Oregano &amp; Thyme with Handmade Gluten-Free Flatbread</p>
      <svg class="tag-icon"><use href="#badge-veg"/></svg><span class="tag-text">GF &nbsp;Dairy Free</span>
      <span class="price">10.99</span>
    </div>
    <div class="item" style="min-height:90px">
      <h3 class="item-name">Sweet Potato Hash</h3>
      <p class="item-desc">Broccolini, Cherry Tomato, Asparagus, Roasted Peppers &amp; Onions, Rosemary-Nutritional Yeast</p>
      <svg class="tag-icon"><use href="#badge-vegan"/></svg><span class="tag-text">GF</span>
      <span class="price">8.99</span>
    </div>
    <div class="item" style="min-height:100px">
      <h3 class="item-name">Mom's Frittata</h3>
      <p class="item-desc">Roasted Cherry Tomato, Goat Cheese &amp; Baby Spinach with Sweet Potato Homefries</p>
      <svg class="tag-icon"><use href="#badge-veg"/></svg><span class="tag-text">GF</span>
      <span class="price">11.99</span>
    </div>
    <div class="item last">
      <h3 class="item-name">Country Style Breakfast Sandwich</h3>
      <p class="item-desc">Arugula, Goat Cheese, Cherry Tomatoes &amp; Lemon with Mom's Frittata on Sprouted 7-Grain Bread</p>
      <svg class="tag-icon"><use href="#badge-veg"/></svg>
      <span class="price">13.99</span>
    </div>
  </div>

  <div class="section-bar" style="top:949px;width:232px">APPETIZERS</div>

  <div class="menu-list" style="top:1013px">
    <div class="item" style="min-height:109px">
      <h3 class="item-name">Avocado Super-Toast</h3>
      <p class="item-desc">Shaved Fennel &amp; Golden Beets, Avocado, Garden Herb Oil, Lemon Juice, Ground Flax, Hemp Seed, Golden Raisin &amp; Moringa on Sprouted 7-Grain Whole</p>
      <svg class="tag-icon"><use href="#badge-vegan"/></svg><span class="tag-text">GF with Flatbread</span>
      <span class="price">9.49</span>
    </div>
    <div class="item last">
      <h3 class="item-name">Pupusa</h3>
      <p class="item-desc">Coconut, Goji, Seasonal Fruit, Crunchy Chia Seeds, Ceylon Cinnamon</p>
      <svg class="tag-icon"><use href="#badge-veg"/></svg><span class="tag-text">GF</span>
      <span class="price">9.49</span>
    </div>
  </div>

  <div class="page-foot"></div>
</section>

<section class="page page-two">
  <div class="brand">Grubb<br>Larder</div>

  <div class="menu-list" style="top:161px">
    <div class="item" style="min-height:86px">
      <h3 class="item-name">Pupusa Deluxe</h3>
      <p class="item-desc">Sous Vide Bison Shortrib, Goat Cheese, Ayocote &amp; Avocado Puree, Nopales, Cilantro-Lime Yogurt, Inca Corn Crumble, Tropical Acai Hot Sauce</p>
      <span class="tag-text">GF</span>
      <span class="price">13.99</span>
    </div>
    <div class="item" style="min-height:108px">
      <h3 class="item-name">Egyptian Flatbread</h3>
      <p class="item-desc">Honey-Chamomile Yogurt, Braised Cherry Tomatoes, Sumac &amp; Pistachio Dukkha, Garlic &amp; Micro Radish on Handmade Gluten-Free Flatbread</p>
      <svg class="tag-icon"><use href="#badge-veg"/></svg><span class="tag-text">GF</span>
      <span class="price">11.99</span>
    </div>
    <div class="item" style="min-height:83px">
      <h3 class="item-name">Green Street Tacos</h3>
      <p class="item-desc">Sugar Snap Peas, Guacamole, Radish &amp; Inca Corn Crumble on 2 Handmade Corn Tortillas.</p>
      <svg class="tag-icon"><use href="#badge-vegan"/></svg><span class="tag-text">GF</span>
      <span class="price">9.99</span>
    </div>
    <div class="item" style="min-height:83px">
      <h3 class="item-name">Marinated Squash Tacos</h3>
      <p class="item-desc">Chayote Escabeche, Jalepeno, Guacamole, Carrots, Radish, Pepitas &amp; Cilantro, on 2 Handmade Corn Tortillas.</p>
      <svg class="tag-icon"><use href="#badge-veg"/></svg><span class="tag-text">GF</span>
      <span class="price">9.99</span>
    </div>
    <div class="item last">
      <h3 class="item-name">Soft Yolk Egg &amp; Avocado "Toast" Flatbread</h3>
      <p class="item-desc">Ayocote &amp; Avocado Puree, Guacamole, Sunflower Seeds, Inca Corn, Arugula, Lime &amp; Soft Yolk Egg on Handmade Gluten-Free Flatbread</p>
      <svg class="tag-icon"><use href="#badge-veg"/></svg><span class="tag-text">GF</span>
      <span class="price">10.99</span>
    </div>
  </div>

  <div class="section-bar" style="top:624px;width:232px">SOUPS</div>

  <div class="menu-list" style="top:689px">
    <div class="item" style="min-height:125px">
      <h3 class="item-name">Seasonal Vegetable Minestrone<br>with Free Range Turkey Meatballs</h3>
      <p class="item-desc">Ayocote Beans, Roasted Tomatoes, Carrots, Onions &amp; Bell Pepper, Snap Peas, Garnett Yam, Rosemary &amp; Oregano</p>
      <span class="tag-text" style="top:12px">GF</span>
      <span class="price" style="top:10px">9.49</span>
    </div>
    <div class="item" style="min-height:89px">
      <h3 class="item-name">Sweet Carrot &amp; Coriander Soup</h3>
      <p class="item-desc">Garden Herb Oil, Cilantro, Toasted Pepitas</p>
      <svg class="tag-icon"><use href="#badge-vegan"/></svg><span class="tag-text">GF</span>
      <span class="price">5.99</span>
    </div>
    <div class="item" style="min-height:127px">
      <h3 class="item-name">Butternut Squash &amp; Nopale Chili</h3>
      <p class="item-desc">Arugula, Goat Cheese, Cherry Tomatoes &amp; Lemon with Mom's Frittata on Sprouted 7-Grain Bread</p>
      <svg class="tag-icon"><use href="#badge-veg"/></svg><span class="tag-text">GF &nbsp;Dairy Free</span>
      <svg class="tag-icon lower"><use href="#badge-vegan"/></svg><span class="tag-text lower">if No Goat Cheese</span>
      <span class="price">13.99</span>
    </div>
    <div class="item last">
      <h3 class="item-name">Rowan's Chicken Soup</h3>
      <p class="item-desc">Gluten-Free Sorghum Penne, Root Vegetables, Oregano &amp; Peppercorns on the Vine</p>
      <span class="tag-text">GF &nbsp;Dairy Free</span>
    </div>
  </div>

  <div class="page-foot"></div>
</section>
</body>
</html>
```